Email Signature Block Design for Law Firm

I would like you to create a similar signature block for my law firm . I saw the email signature block attached as image002.png and wanted a similar design for my law firm. I want to be able to swap the portraits for each of my staff from the final design. Our law firm colors are black, gold, white, red.

Industry/Entity Type

Law

Requirements
Nice to have
• i like the red circle in around the photo in the tall oak group design. The Silver Lark Co desgn is what inspired me to have a signature block design for my firm.

```html
<!DOCTYPE html>
<html lang="en">
<head>
<meta charset="utf-8">
<title>The Hartwell Firm – Email Signature</title>
<link rel="stylesheet" href="https://fonts.googleapis.com/css2?family=Cinzel:wght@400;500&family=Marcellus&family=Montserrat:wght@500&display=swap">
<style>
  :root {
    --paper: #ffffff;
    --ink: #111111;
    --band: #000000;
    --gold: #c9961f;
    --firm-ink: #4a4a4a;
    --muted: #9a9a9a;
    --accent-red: #d71f26;
    --faint: #f1f1f1;
    --photo-light: #c9c9c9;
    --photo-dark: #2a2c33;
  }
  * { margin: 0; padding: 0; box-sizing: border-box; }
  html, body { width: 1200px; height: 400px; overflow: hidden; background: var(--paper); }
  .signature {
    position: relative;
    width: 1200px;
    height: 400px;
    background: var(--paper);
    overflow: hidden;
  }
  .backdrop-mark {
    position: absolute;
    left: 750px;
    top: 20px;
    width: 380px;
    height: 284px;
    background: var(--faint);
  }
  .firm-mark {
    position: absolute;
    left: 39px;
    top: 44px;
    display: flex;
    align-items: center;
    gap: 12px;
  }
  .firm-mark__square {
    width: 40px;
    height: 40px;
    background: var(--gold);
  }
  .firm-mark__name {
    font-family: "Cinzel", serif;
    font-weight: 500;
    font-size: 19px;
    color: var(--firm-ink);
    letter-spacing: 0.5px;
  }
  .person {
    position: absolute;
    left: 42px;
    top: 160px;
  }
  .person__name {
    font-family: "Cinzel", serif;
    font-weight: 400;
    font-size: 43px;
    line-height: 1;
    color: var(--ink);
    letter-spacing: 1px;
  }
  .person__title {
    margin-top: 12px;
    font-family: "Montserrat", sans-serif;
    font-weight: 500;
    font-size: 16px;
    letter-spacing: 2.5px;
    color: var(--muted);
  }
  .contact-band {
    position: absolute;
    left: 0;
    top: 304px;
    width: 1200px;
    height: 96px;
    background: var(--band);
  }
  .contact-list {
    position: absolute;
    list-style: none;
    font-family: "Marcellus", serif;
    font-size: 20px;
    color: var(--paper);
  }
  .contact-list li {
    display: flex;
    align-items: center;
    gap: 12px;
    height: 27px;
  }
  .contact-list--left { left: 41px; top: 322px; }
  .contact-list--right { right: 20px; top: 322px; }
  .contact-list--right li { justify-content: flex-end; }
  .contact-icon { width: 14px; height: 14px; flex: none; }
  .social-dot {
    width: 11px;
    height: 11px;
    border: 1.6px solid var(--accent-red);
    border-radius: 3px;
    flex: none;
    margin: 0 2px;
  }
  .portrait-ring {
    position: absolute;
    left: 459px;
    top: 59px;
    width: 318px;
    height: 318px;
    border-radius: 50%;
    background: var(--accent-red);
    padding: 21px;
  }
  .portrait {
    width: 100%;
    height: 100%;
    border-radius: 50%;
    background: radial-gradient(circle at 50% 35%, var(--photo-light) 0%, #8d8a88 45%, var(--photo-dark) 100%);
  }
</style>
</head>
<body>
  <main class="signature">
    <div class="backdrop-mark" aria-hidden="true"></div>

    <div class="firm-mark">
      <span class="firm-mark__square" aria-hidden="true"></span>
      <span class="firm-mark__name">The Hartwell Firm, PLLC</span>
    </div>

    <div class="person">
      <h1 class="person__name">Name Surname</h1>
      <p class="person__title">TITLE</p>
    </div>

    <div class="contact-band"></div>

    <ul class="contact-list contact-list--left">
      <li>
        <svg class="contact-icon" viewBox="0 0 24 24" aria-hidden="true">
          <path fill="#d71f26" d="M6.6 10.8a15.1 15.1 0 0 0 6.6 6.6l2.2-2.2a1 1 0 0 1 1-.25 11.4 11.4 0 0 0 3.6.57 1 1 0 0 1 1 1V20a1 1 0 0 1-1 1A17 17 0 0 1 3 4a1 1 0 0 1 1-1h3.5a1 1 0 0 1 1 1c0 1.25.2 2.45.57 3.57a1 1 0 0 1-.25 1z"/>
        </svg>
        <span>205-555-0148</span>
      </li>
      <li>
        <svg class="contact-icon" viewBox="0 0 24 24" aria-hidden="true">
          <rect x="2" y="5" width="20" height="14" fill="#d71f26"/>
          <path d="M2 5l10 8 10-8" fill="none" stroke="#000" stroke-width="1.6"/>
        </svg>
        <span>contact@hartwell-firm.com</span>
      </li>
    </ul>

    <ul class="contact-list contact-list--right">
      <li>
        <span>hartwellfirmlaw</span>
        <span class="social-dot" aria-hidden="true"></span>
      </li>
      <li>
        <span>Bayport, FL</span>
        <svg class="contact-icon" viewBox="0 0 24 24" aria-hidden="true">
          <path d="M12 2a7 7 0 0 0-7 7c0 5 7 13 7 13s7-8 7-13a7 7 0 0 0-7-7z" fill="none" stroke="#d71f26" stroke-width="2.2"/>
          <circle cx="12" cy="9" r="2.4" fill="#d71f26"/>
        </svg>
      </li>
    </ul>

    <div class="portrait-ring">
      <div class="portrait" role="img" aria-label="Staff portrait: smiling attorney in a dark suit and blue striped tie"></div>
    </div>
  </main>
</body>
</html>
```